New Business Card Design Project LORVANTI-Italy

we are LORVANTI-Italy
our company in the market for 3 years we are luxury cosmetic company and its about time for a facelift :)
i will like to have elegant luxurious and unique business card
that will give the person that get it a unique, luxurious and elegant impression
I'm VERY OPEN FOR NEW IDEAS , even duo i add a few files of things that i see on line and i like them

i add my logo as well
my website is LORVANTI.COM
(if you would like to see the main style that we have)

Target Market(s)

adult that have money :)

Industry/Entity Type

Business

Contact Information for Business Card

Name - Dario Lorvanti
Position - CEO and CO Founder
address - 4817 E Halvern
telephone - 555-384-1926
email - dario@lorvanti.com
fax - 555-384-1926
website - LORVANTI.COM

Colors
000000
959595
fbee3e
ffffff

Requirements
Must have
• big logo in GOLD color
• elegant look
• impressive
Nice to have
• not must but maybe classy pattern background
• not must but maybe emblem
• maybe clear plastic business card
Should not have
• colors
• images

```html
<!DOCTYPE html>
<html lang="en">
<head>
<meta charset="utf-8">
<title>LORVANTI-Italy Business Card</title>
<link rel="stylesheet" href="https://fonts.googleapis.com/css2?family=EB+Garamond:wght@400;600&display=swap">
<style>
  :root {
    --backdrop: #1d1d1d;
    --card: #111111;
    --card-edge: #2a2a2a;
    --gold: #c9a43a;
    --white: #f2f2f2;
  }
  * { margin: 0; padding: 0; box-sizing: border-box; }
  html, body {
    width: 1200px;
    height: 833px;
    overflow: hidden;
    background: var(--backdrop);
    font-family: "EB Garamond", Georgia, serif;
  }
  .canvas {
    position: relative;
    width: 1200px;
    height: 833px;
  }
  .card {
    position: absolute;
    top: 262px;
    width: 540px;
    height: 309px;
    background: var(--card);
    border: 1px solid var(--card-edge);
    box-shadow: 0 18px 40px rgba(0, 0, 0, 0.55);
  }
  .card--front { left: 40px; }
  .card--back { left: 620px; }

  /* Front: brand mark */
  .front-mark {
    position: absolute;
    left: 50%;
    top: 50%;
    transform: translate(-50%, -50%);
    display: flex;
    flex-direction: column;
    align-items: center;
    gap: 14px;
  }
  .brand-dot {
    width: 74px;
    height: 74px;
    border-radius: 50%;
    background: var(--gold);
  }
  .brand-name {
    color: var(--gold);
    font-weight: 400;
    font-size: 30px;
    letter-spacing: 2px;
    line-height: 1;
    white-space: nowrap;
  }

  /* Back: contact details */
  .contact {
    position: absolute;
    left: 40px;
    top: 38px;
    color: var(--white);
    font-size: 16px;
    line-height: 1.3;
  }
  .contact__name {
    color: var(--gold);
    font-weight: 600;
    font-size: 24px;
    line-height: 1.1;
  }
  .contact__role { margin-bottom: 10px; }
  .contact__company { color: var(--gold); font-weight: 600; }
  .contact__address { margin-bottom: 12px; }
  .contact__row {
    display: flex;
    gap: 6px;
    white-space: nowrap;
  }
  .contact__label {
    color: var(--gold);
    flex: 0 0 28px;
    white-space: nowrap;
  }

  .back-mark {
    position: absolute;
    right: 36px;
    bottom: 40px;
    display: flex;
    flex-direction: column;
    align-items: center;
    gap: 12px;
  }
  .back-mark .brand-dot { width: 60px; height: 60px; }
  .back-mark .brand-name { font-size: 34px; }
</style>
</head>
<body>
<main class="canvas">
  <section class="card card--front" aria-label="Card front">
    <div class="front-mark">
      <span class="brand-dot"></span>
      <span class="brand-name">LORVANTI</span>
    </div>
  </section>

  <section class="card card--back" aria-label="Card back">
    <div class="contact">
      <p class="contact__name">Dario Lorvanti</p>
      <p class="contact__role">CEO and CO Founder</p>
      <p class="contact__company">LORVANTI-Italy</p>
      <p class="contact__address">4817 E Halvern</p>
      <p class="contact__row"><span class="contact__label">T :</span><span>555-384-1926</span></p>
      <p class="contact__row"><span class="contact__label">F :</span><span>555-384-1926</span></p>
      <p class="contact__row"><span class="contact__label">E :</span><span>dario@lorvanti.com</span></p>
      <p class="contact__row"><span class="contact__label">W :</span><span>lorvanti.com</span></p>
    </div>
    <div class="back-mark">
      <span class="brand-dot"></span>
      <span class="brand-name">LORVANTI</span>
    </div>
  </section>
</main>
</body>
</html>
```